Stylish business cards for KV7

To create an appealing and professional business card design for a WOMEN Owned Construction Supply Company.
2 sided card. Incorporate brand elements, curvy, colorful, sleek and bright. No solid white background. attached samples of styles added shapes/ribbons. Want something with that WOW that looks awesome, factor. It is a new logo, so feel free to mess with logo colors in the blue and teal factors that can look good with both dark and light background. If you want to try a watermark with just the KV7, without the "Supply" that might look cool to.

Industry/Entity Type

Women owned construction supply company

Contact Information for Business Card

Name, Title, and phone number and email, web page. maybe spot for qr code.

Font styles to use
Sans Serif

Requirements
Nice to have
• would love to see colors, maybe stylish ribbon dividers or some sort of 2 or 3 tone color card that compliments logo.
Should not have
• Please do not have all white background. Do not include Home/reale state/ or building images.

```html
<!DOCTYPE html>
<html lang="en">
<head>
<meta charset="utf-8">
<title>KV7 Supply — Business Card</title>
<link href="https://fonts.googleapis.com/css2?family=Poppins:wght@400;500;600&display=swap" rel="stylesheet">
<style>
  :root {
    --backdrop: #e3e8ea;
    --brand-blue: #1e95bc;
    --brand-navy: #1d3f66;
    --card-light: #f2f2f2;
    --ink: #111111;
    --mark-light: #d6eaf3;
    --white: #ffffff;
  }
  * { box-sizing: border-box; margin: 0; padding: 0; }
  html, body {
    width: 1200px; height: 960px; overflow: hidden;
    background: var(--backdrop);
    font-family: "Poppins", sans-serif;
  }
  .card {
    position: absolute; left: 250px; width: 701px; height: 400px; overflow: hidden;
  }
  .card-front { top: 60px; background: var(--brand-blue); }
  .card-back { top: 500px; background: var(--card-light); }

  .front-wordmark {
    position: absolute; left: 0; right: 0; top: 128px;
    text-align: center; font-size: 112px; font-weight: 600; letter-spacing: 4px;
    color: var(--mark-light); line-height: 1;
  }

  .back-wordmark {
    position: absolute; left: 26px; top: 58px;
    display: flex; align-items: center; gap: 10px;
    font-size: 46px; font-weight: 600; color: var(--brand-navy); line-height: 1;
  }
  .back-wordmark .dot { width: 14px; height: 14px; border-radius: 50%; background: var(--brand-blue); }
  .back-wordmark .sub { display: block; font-size: 22px; margin-top: 6px; }

  .identity { position: absolute; right: 29px; top: 24px; text-align: right; }
  .identity .name { font-size: 33px; line-height: 1.1; color: var(--brand-blue); letter-spacing: 1px; }
  .identity .name b { font-weight: 600; }
  .identity .name span { font-weight: 400; }
  .identity .title { font-size: 17px; font-weight: 500; color: var(--ink); margin-top: 2px; letter-spacing: 0.5px; }
  .accent-bar { position: absolute; left: 682px; top: 31px; width: 19px; height: 53px; background: var(--brand-blue); }

  .address {
    position: absolute; left: 28px; top: 196px;
    font-size: 18px; line-height: 26px; color: var(--brand-blue); letter-spacing: 0.3px;
  }

  .contact-band { position: absolute; left: 0; top: 0; }
  .contacts { position: absolute; left: 24px; top: 296px; list-style: none; }
  .contacts li {
    display: flex; align-items: center; gap: 12px; height: 26px;
    font-size: 19px; color: var(--white); letter-spacing: 0.3px;
  }
  .contacts svg { width: 17px; height: 17px; flex: none; }

  .corner-mark {
    position: absolute; right: 26px; bottom: 14px;
    font-size: 64px; font-weight: 600; color: var(--brand-navy); line-height: 1;
  }
</style>
</head>
<body>

<section class="card card-front" aria-label="Card front">
  <div class="front-wordmark">KV7</div>
</section>

<section class="card card-back" aria-label="Card back">
  <svg class="contact-band" width="701" height="400" viewBox="0 0 701 400" aria-hidden="true">
    <polygon points="0,268 610,268 555,400 0,400" fill="var(--brand-blue)"/>
  </svg>

  <div class="back-wordmark">
    <span class="dot"></span>
    <div>KV7<span class="sub">Supply</span></div>
  </div>

  <div class="identity">
    <div class="name"><b>Marta</b> <span>Kovacs</span></div>
    <div class="title">Founder &amp; CEO</div>
  </div>
  <div class="accent-bar"></div>

  <address class="address" style="font-style:normal">
    4180 Linden Ave. Suite 310<br>
    Dayton, OH 45402
  </address>

  <ul class="contacts">
    <li>
      <svg viewBox="0 0 24 24" aria-hidden="true"><path fill="#fff" d="M6.6 10.8a15.1 15.1 0 0 0 6.6 6.6l2.2-2.2c.3-.3.7-.4 1-.2 1.1.4 2.3.6 3.6.6.6 0 1 .4 1 1V20c0 .6-.4 1-1 1A17 17 0 0 1 3 4c0-.6.4-1 1-1h3.5c.6 0 1 .4 1 1 0 1.3.2 2.5.6 3.6.1.3 0 .7-.2 1z"/></svg>
      (555) 014-2286
    </li>
    <li>
      <svg viewBox="0 0 24 24" aria-hidden="true"><circle cx="12" cy="12" r="10" fill="none" stroke="#fff" stroke-width="2"/><path d="M2 12h20M12 2c3 3 3 17 0 20M12 2c-3 3-3 17 0 20" fill="none" stroke="#fff" stroke-width="1.6"/></svg>
      info@yourwebsite.com
    </li>
    <li>
      <svg viewBox="0 0 24 24" aria-hidden="true"><rect x="2" y="5" width="20" height="14" rx="1" fill="#fff"/><path d="M2 6l10 7 10-7" fill="none" stroke="var(--brand-blue)" stroke-width="1.6"/></svg>
      www.yourwebsite.com
    </li>
  </ul>

  <div class="corner-mark">KV7</div>
</section>

</body>
</html>
```